LEARN Business Skills so you can Earn a good living

size of the poster is 8”x 10.75" plus 0.25" bleed.
Please leave 1 inch on the bottoum for footer
I want a design a poster that will attract people's attention.
I appreciate a creative ad however the ad should not take away from being able to clearly read the text.
-I also appreciate a simple creative ad that is not too busy.
-you can use graphics, vectors, or pictures of real people.
-however, if you use real people it should be a white male that is wearing a white shirt and look like a professional person.

Target Market(s)

Potential young business people

Industry/Entity Type

education

Requirements
Must have
• easy to read the text
Nice to have
• I would like a "creative" simple ad that is easy to be read
Should not have
• pictures of women

```html
<!DOCTYPE html>
<html lang="en">
<head>
<meta charset="UTF-8">
<title>Learn It To Earn It – Business Enrichment Course</title>
<link rel="stylesheet" href="https://fonts.googleapis.com/css2?family=Poppins:wght@300;400;600;700;800&display=swap">
<style>
  :root {
    --ink: #1f1f1f;
    --paper: #ffffff;
    --band: #232323;
    --rule: #cfcfcf;
    --photo-light: #f4f4f4;
    --photo-mid: #d9d9d9;
    --photo-dark: #8a8a8a;
    --icon-fill: #6e6e6e;
    --line-light: #e8e8e8;
  }
  * { margin: 0; padding: 0; box-sizing: border-box; }
  html, body { width: 800px; height: 1200px; overflow: hidden; background: var(--paper); }
  body { font-family: "Poppins", sans-serif; color: var(--ink); }

  .poster { position: relative; width: 800px; height: 1200px; overflow: hidden; background: var(--paper); }

  .hero { position: absolute; left: 0; top: 0; width: 800px; height: 816px; }
  .hero-photo {
    position: absolute; inset: 0;
    background:
      radial-gradient(ellipse 260px 380px at 610px 560px, var(--photo-dark) 0%, rgba(138,138,138,0.55) 45%, rgba(217,217,217,0) 100%),
      linear-gradient(90deg, var(--paper) 0%, var(--photo-light) 35%, var(--photo-mid) 100%);
  }

  .headline { position: absolute; left: 40px; line-height: 1; letter-spacing: -3px; white-space: nowrap; }
  .headline-main { top: 62px; font-size: 154px; }
  .headline-sub { top: 228px; font-size: 100px; letter-spacing: -2px; }
  .headline strong { font-weight: 800; }
  .headline .light { font-weight: 300; }

  .divider { position: absolute; left: 43px; height: 1px; background: var(--rule); }
  .divider-top { top: 362px; width: 500px; }
  .divider-mid { top: 611px; width: 330px; }

  .course-title {
    position: absolute; left: 42px; top: 392px;
    font-size: 62px; font-weight: 800; line-height: 64px; letter-spacing: -0.5px; text-transform: uppercase;
  }
  .tagline {
    position: absolute; left: 43px; top: 640px;
    font-size: 31px; font-weight: 600; line-height: 38px; letter-spacing: -0.3px;
  }

  .skills-band { position: absolute; left: 0; top: 816px; width: 800px; height: 384px; background: var(--band); color: var(--paper); }

  .skills-box {
    position: absolute; left: 54px; top: 72px; width: 692px; height: 188px;
    border: 1.5px solid var(--line-light); border-radius: 16px;
  }
  .skills-heading {
    position: absolute; left: 98px; top: 42px; width: 606px; height: 48px;
    background: var(--paper); color: var(--ink); border-radius: 24px;
    font-size: 28px; font-weight: 700; line-height: 48px; text-align: center; letter-spacing: 0.3px;
    z-index: 2;
  }
  .skill-list { position: absolute; left: 54px; top: 110px; width: 692px; height: 140px; display: flex; }
  .skill { position: relative; display: flex; flex-direction: column; align-items: center; }
  .skill:nth-child(1) { width: 228px; }
  .skill:nth-child(2) { width: 235px; }
  .skill:nth-child(3) { width: 229px; }
  .skill + .skill::before {
    content: ""; position: absolute; left: 0; top: 0; width: 1px; height: 124px; background: #6a6a6a;
  }
  .skill-icon {
    width: 56px; height: 56px; border-radius: 50%;
    background: var(--icon-fill); border: 2px solid var(--line-light);
    display: flex; align-items: center; justify-content: center;
  }
  .skill-label { margin-top: 10px; font-size: 21px; font-weight: 600; line-height: 24px; text-align: center; }

  .topic-list {
    position: absolute; left: 0; top: 280px; width: 800px;
    font-size: 12px; font-weight: 400; line-height: 15px; text-align: center; letter-spacing: 0.1px;
    text-transform: uppercase;
  }
</style>
</head>
<body>
<main class="poster">
  <section class="hero">
    <div class="hero-photo" role="img" aria-label="Photo of a smiling young businessman in a dark suit, white shirt and blue tie, seated at a desk in a bright office"></div>

    <h1 class="headline headline-main"><strong>LEARN</strong> <span class="light">IT</span></h1>
    <p class="headline headline-sub"><span class="light">TO</span> <strong>EARN</strong> <span class="light">IT</span></p>

    <div class="divider divider-top"></div>
    <h2 class="course-title">Business<br>Enrichment<br>Course</h2>
    <div class="divider divider-mid"></div>
    <p class="tagline">A proven success of<br>helping people in<br>their livelihoods</p>
  </section>

  <section class="skills-band">
    <div class="skills-box"></div>
    <h3 class="skills-heading">BUSINESS SKILLS THAT WILL HELP YOU</h3>

    <ul class="skill-list">
      <li class="skill">
        <span class="skill-icon">
          <svg width="30" height="30" viewBox="0 0 30 30" fill="none" stroke="#fff" stroke-width="1.6" stroke-linecap="round" stroke-linejoin="round">
            <rect x="5" y="3" width="20" height="15" rx="2"/>
            <circle cx="15" cy="13" r="4"/>
            <path d="M9 7h2M14 7h2M19 7h2"/>
            <path d="M12 17l-2 9 5-3 5 3-2-9"/>
          </svg>
        </span>
        <span class="skill-label">Get a<br>quality job</span>
      </li>
      <li class="skill">
        <span class="skill-icon">
          <svg width="30" height="30" viewBox="0 0 30 30" fill="none" stroke="#fff" stroke-width="1.6" stroke-linecap="round" stroke-linejoin="round">
            <rect x="5" y="18" width="4" height="7"/>
            <rect x="11" y="15" width="4" height="10"/>
            <rect x="17" y="12" width="4" height="13"/>
            <path d="M4 14l7-5 5 3 9-7"/>
            <path d="M21 5h4v4"/>
          </svg>
        </span>
        <span class="skill-label">Start/grow<br>your business</span>
      </li>
      <li class="skill">
        <span class="skill-icon">
          <svg width="30" height="30" viewBox="0 0 30 30" fill="none" stroke="#fff" stroke-width="1.6" stroke-linecap="round" stroke-linejoin="round">
            <rect x="4" y="14" width="22" height="11" rx="1"/>
            <circle cx="15" cy="19.5" r="2.5"/>
            <path d="M4 10l7-4 5 3 9-6"/>
            <path d="M21 3h4v4"/>
          </svg>
        </span>
        <span class="skill-label">Increase your<br>salary</span>
      </li>
    </ul>

    <p class="topic-list">
      Business Administration&nbsp; | &nbsp;Small Business Management&nbsp; | &nbsp;Finance | Investments&nbsp; | &nbsp;Computers&nbsp; | &nbsp;Accounting<br>
      Sales&nbsp; | &nbsp;Marketing&nbsp; | &nbsp;Project Management Interviewing Skills&nbsp; | &nbsp;Business Law&nbsp; | &nbsp;Negotiation&nbsp; | &nbsp;Public Speaking<br>
      Import/Export&nbsp; | &nbsp;Information Technology&nbsp; | &nbsp;Distribution&nbsp; | &nbsp;Marketing&nbsp; | &nbsp;LedgerPro&nbsp; | &nbsp;Real Estate<br>
      Health Care-Management&nbsp; | &nbsp;MarketHub
    </p>
  </section>
</main>
</body>
</html>
```